Vorelan.com Personal Trainer/Fitness Website

I want a website to market my personal training/Outdoor Bootcamp Class services, as well as to ditribute nutrivex. I need a logo as well I included an address for the Harbor Gales 1975 logo. I'd like Vorelan in place of Harbor Gales, and in Black and white, just different enough so I can't get sued by the PBL.
https://www.pictofind.example/imgres?imgurl=http%3A%2F%2Fwww.darnell-quibury.example%2Fwp-content%2Fuploads%2F2014%2F01%2Fgales_logo4.jpg&imgrefurl=http%3A%2F%2Fwww.darnell-quibury.example%2Fpbl-logo-redesigns-harbor-gales%2F&docid=_qkwzR7TBAgXpL&tbnid=m4tpU8KdOXjnRP%3A&w=600&h=450&client=ms-android-carrier&bih=512&biw=360&ved=0ahUKEwiRtpgyp9HMAhUTwGMKHRPMBWMQMwg6KBQwFA&iact=mrc&uact=8.
It should be about 5 pages 1. home 2. about 3. Services 4. Blog/Videos and programs 5. Contact.
http://www.dorvinfitness.example.uk/ is a website I like the style of.

Target Market(s)

Seattle area

Industry/Entity Type

Fitness

Coding

Coded - Design and coding required

Number of Pages Required

4 page

Font styles to use
Serif
Sans Serif

Requirements
Must have
• A minimal look
Nice to have
• A logo similar to the 1975 Harbor Galewinds Logo, with a Small Milo Brandt ripping his shirt open(with a picture of the logo on his shirt, picture within picture) to turn into Ironjaw in the center. Skyline is black, Background and small figure white(with black logo on shirt)

```html
<!DOCTYPE html>
<html lang="en">
<head>
<meta charset="utf-8">
<title>Vorelan – Personal Training &amp; Outdoor Bootcamp</title>
<link rel="stylesheet" href="https://fonts.googleapis.com/css2?family=Federo&family=Mulish:ital,wght@0,400;0,600;0,700;0,800;1,400&display=swap">
<style>
:root{
  --ink:#111111;
  --text:#2a2a2a;
  --muted:#6d6d6d;
  --white:#ffffff;
  --panel:#eceef2;
  --arrow-box:#c4c6ca;
  --footer:#2f2f2f;
  --footer-line:#5a5a5a;
  --footer-text:#d6d6d6;
  --bottom-bar:#1b1b1b;
  --follow-tab:#d9d9d9;
  --social:#8d9096;
  --grass-a:#5f8a3a;
  --grass-b:#34502a;
}
*{margin:0;padding:0;box-sizing:border-box}
html,body{width:1200px;height:2571px;overflow:hidden}
body{position:relative;background:var(--white);font-family:"Mulish",sans-serif;color:var(--text)}
.abs{position:absolute}
.display{font-family:"Federo",sans-serif}

/* header */
.site-header{left:0;top:0;width:1200px;height:112px;background:var(--white);border-bottom:1px solid #d8d8d8}
.brand{left:103px;top:14px;display:flex;flex-direction:column;align-items:center;width:112px}
.brand-mark{width:56px;height:56px;border-radius:50%;background:var(--ink)}
.brand-name{font-family:"Federo",sans-serif;font-size:17px;letter-spacing:2px;color:var(--ink);margin-top:4px}
.main-nav{left:0;top:75px;width:1200px;height:20px}
.main-nav a{position:absolute;font-family:"Federo",sans-serif;font-size:13px;color:var(--ink);text-decoration:none;letter-spacing:.3px}
.main-nav a.active::after{content:"";position:absolute;left:-4px;right:-4px;top:30px;height:2px;background:var(--ink)}
.social{display:flex;gap:7px}
.social span{width:27px;height:27px;background:var(--social);display:block}
.header-social{left:722px;top:24px}
.call{left:908px;top:18px;display:flex;align-items:center;gap:10px}
.call-icon{width:30px;height:30px;border-radius:50%;border:1.5px solid var(--ink);display:flex;align-items:center;justify-content:center}
.call-label{font-size:9px;color:var(--muted);letter-spacing:1px}
.call-number{font-family:"Federo",sans-serif;font-size:23px;color:var(--ink);line-height:1}

/* hero */
.hero{left:0;top:112px;width:1200px;height:442px;background:linear-gradient(160deg,#7ea657 0%,var(--grass-a) 40%,var(--grass-b) 100%)}
.hero-shade{left:0;top:112px;width:1200px;height:442px;background:linear-gradient(90deg,rgba(0,0,0,.25),rgba(0,0,0,0) 60%)}
.hero-title{left:99px;top:285px;width:364px;height:80px;background:rgba(0,0,0,.72);color:var(--white);font-family:"Mulish",sans-serif;font-weight:600;font-size:29px;line-height:36px;padding:5px 10px;text-transform:uppercase}
.btn{display:flex;align-items:center;justify-content:space-between;font-family:"Federo",sans-serif;font-size:14px;text-decoration:none;padding:0 14px}
.btn-light{background:var(--white);color:var(--ink)}
.btn-dark{background:var(--ink);color:var(--white)}
.btn-dark .arrow-dot{background:var(--white)}
.btn-dark .arrow-dot path{stroke:var(--ink)}
.arrow-dot{width:22px;height:22px;border-radius:50%;background:var(--ink);display:flex;align-items:center;justify-content:center}
.arrow-dot path{stroke:var(--white)}
.hero-btn{left:99px;top:381px;width:150px;height:39px}

/* about */
.about{left:0;top:554px;width:1200px;height:329px;background:var(--panel)}
.about-photo{left:120px;top:586px;width:300px;height:297px;background:linear-gradient(180deg,#c9a58a,#8e6a52);border-radius:140px 140px 0 0}
.section-title{font-family:"Federo",sans-serif;color:var(--ink);font-size:32px}
.about-title{left:463px;top:592px}
.about-rule{left:668px;top:624px;width:78px;height:1px;background:#9a9a9a}
.about-text{left:463px;top:645px;width:640px;font-size:12.5px;line-height:28.5px;color:var(--text)}
.about-btn{left:465px;top:804px;width:150px;height:39px}

/* services */
.services-title{left:0;top:920px;width:1200px;text-align:center}
.title-rule{height:2px;width:80px;background:#c8c8c8}
.services-rule{left:560px;top:972px}
.service-card{top:1006px;width:275px;height:295px;background:var(--panel)}
.service-img{width:275px;height:151px}
.service-card h3{font-family:"Mulish",sans-serif;font-weight:600;font-size:19px;color:var(--ink);margin:20px 19px 8px}
.service-card p{font-size:12px;line-height:22px;margin:0 19px;color:var(--text)}
.arrow-box{position:absolute;right:0;bottom:0;width:36px;height:34px;background:var(--arrow-box);display:flex;align-items:center;justify-content:center}
.services-btn{left:500px;top:1335px;width:199px;height:41px}

/* videos */
.videos{left:0;top:1416px;width:1200px;height:432px;background:linear-gradient(180deg,#e4e5e7 0%,#cfd1d4 55%,#b9bbbf 100%)}
.videos-title{left:0;top:1466px;width:1200px;text-align:center}
.videos-rule{left:560px;top:1518px}
.coach-photo{left:26px;top:1517px;width:248px;height:331px;background:linear-gradient(180deg,#6a4a3a,#9ea3a8 55%,#7d8288);border-radius:110px 110px 0 0}
.program-list{left:305px;top:1565px;list-style:none;font-size:12.5px;line-height:27.5px;color:var(--text)}
.program-list li::before{content:"";display:inline-block;width:5px;height:5px;background:var(--ink);margin:0 10px 2px 0}
.video-frame{left:756px;top:1568px;width:346px;height:206px;border:3px solid #4f4f4f;background:linear-gradient(180deg,#cfd68a 0%,#6f9a3e 55%,#4d7a2b 100%);display:flex;align-items:center;justify-content:center}
.play{width:46px;height:46px;border-radius:50%;border:2px solid var(--ink);background:rgba(255,255,255,.35);display:flex;align-items:center;justify-content:center}
.videos-link{left:862px;top:1789px;display:flex;align-items:center;gap:10px;font-family:"Federo",sans-serif;font-size:14px;color:var(--ink)}

/* blog */
.blog-title{left:0;top:1893px;width:1200px;text-align:center}
.blog-rule{left:560px;top:1945px}
.blog-card{top:1980px;width:476px;height:204px;background:var(--panel);display:flex}
.blog-img{width:206px;height:204px;flex:none}
.blog-body{padding:14px 14px 0 14px}
.blog-body h3{font-weight:700;font-size:16px;line-height:20px;color:var(--ink)}
.blog-date{font-style:italic;font-size:11px;color:var(--muted);margin:6px 0 4px}
.blog-body p{font-size:12px;line-height:21px}

/* footer */
.site-footer{left:0;top:2254px;width:1200px;height:283px;background:var(--footer)}
.footer-col h4{font-family:"Federo",sans-serif;font-weight:400;font-size:18px;color:var(--white);padding-bottom:10px;border-bottom:1px solid var(--footer-line);width:196px}
.footer-links{list-style:none;margin-top:12px;font-size:12.5px;color:var(--footer-text);line-height:29px}
.footer-links li::before{content:"";display:inline-block;width:6px;height:6px;border:1.5px dotted var(--footer-text);margin:0 10px 2px 0}
.contact-list{list-style:none;margin-top:12px;font-size:12.5px;color:var(--footer-text);line-height:25px}
.contact-list li{display:flex;gap:12px;align-items:flex-start;margin-bottom:4px}
.contact-list svg{flex:none;margin-top:5px}
.field{background:var(--white);font-size:10px;color:var(--muted);padding:5px 10px;width:216px}
.submit{width:110px;height:34px;margin-top:11px}
.footer-brand{left:857px;top:2288px;width:220px;height:215px;display:flex;flex-direction:column;align-items:center;justify-content:center;gap:12px}
.footer-brand .brand-mark{width:120px;height:120px;background:#8a8a8a}
.footer-brand .brand-name{color:#8a8a8a;font-size:30px;letter-spacing:4px}
.bottom-bar{left:0;top:2537px;width:1200px;height:34px;background:var(--bottom-bar)}
.copyright{left:99px;top:2547px;font-size:12px;color:var(--footer-text)}
.copyright b{color:var(--white)}
.follow-tab{left:780px;top:2520px;width:420px;height:51px;background:var(--follow-tab);border-radius:40px 0 0 0;display:flex;align-items:center;padding-left:54px;gap:16px}
.follow-tab .label{font-family:"Federo",sans-serif;font-size:17px;color:var(--ink)}
</style>
</head>
<body>

<header class="abs site-header">
  <div class="abs brand"><span class="brand-mark"></span><span class="brand-name">VORELAN</span></div>
  <div class="abs social header-social"><span></span><span></span><span></span><span></span></div>
  <div class="abs call">
    <span class="call-icon"><svg width="14" height="14" viewBox="0 0 24 24"><path d="M6 2l4 4-2 3c1 3 4 6 7 7l3-2 4 4-3 4C10 21 3 14 2 5z" fill="#111"/></svg></span>
    <div><div class="call-label">CALL US NOW :</div><div class="call-number">012. 345. 6789</div></div>
  </div>
  <nav class="main-nav abs">
    <a class="active" style="left:408px">HOME</a>
    <a style="left:505px">ABOUT</a>
    <a style="left:605px">SERVICES</a>
    <a style="left:722px">BLOG</a>
    <a style="left:814px">VIDEOS AND PROGRAMS</a>
    <a style="left:1033px">CONTACT</a>
  </nav>
</header>

<section>
  <div class="abs hero" role="img" aria-label="Trainer leading an outdoor bootcamp group doing exercises on grass"></div>
  <div class="abs hero-shade"></div>
  <h1 class="abs hero-title">Get Fit! Get Strong!<br>Get Outdoors!</h1>
  <a class="abs btn btn-light hero-btn">Get Started <span class="arrow-dot"><svg width="12" height="12" viewBox="0 0 12 12"><path d="M2 6h8M7 3l3 3-3 3" fill="none" stroke-width="1.8"/></svg></span></a>
</section>

<section>
  <div class="abs about"></div>
  <div class="abs about-photo" role="img" aria-label="Smiling muscular trainer, shirtless, hands on hips"></div>
  <h2 class="abs section-title about-title">About Vorelan</h2>
  <div class="abs about-rule"></div>
  <p class="abs about-text">Lorem ipsum dolor sit amet, consectetuer adipiscing elit, sed diam nonummy nibh euismod tincid laoreet dolore magna aliquam erat volutpat. Ut wisi enim ad minim veniam, quis nostrud exerci tati ullamcorper suscipit lobortis nisl ut aliquip ex ea commodo consequat. Duis autem vel eum iriure dolor in hendreri in vulputate velit esse molestie consequat, vel illum dolore eu feugiat nulla facilisis at vero eros et accumsan et iusto odio dignissim qui blandit praesent luptatum zzril dolore te feugait...</p>
  <a class="abs btn btn-dark about-btn">Learn More <span class="arrow-dot"><svg width="12" height="12" viewBox="0 0 12 12"><path d="M2 6h8M7 3l3 3-3 3" fill="none" stroke-width="1.8"/></svg></span></a>
</section>

<section>
  <h2 class="abs section-title services-title">Our Services</h2>
  <div class="abs title-rule services-rule"></div>

  <article class="abs service-card" style="left:123px">
    <div class="service-img" role="img" aria-label="Trainer coaching a client through a personal training session in a park" style="background:linear-gradient(180deg,#8aa0a8,#5d7a45)"></div>
    <h3>Personal Training</h3>
    <p>Magna aliquam erat volutpat. Ut niml ad minim veniam, quis naullamcorper suscipit commodo consequat.</p>
    <span class="arrow-box"><svg width="10" height="14" viewBox="0 0 10 14"><path d="M2 1l6 6-6 6" fill="none" stroke="#fff" stroke-width="2"/></svg></span>
  </article>

  <article class="abs service-card" style="left:459px">
    <div class="service-img" role="img" aria-label="Group doing sit-ups together in an outdoor bootcamp" style="background:linear-gradient(180deg,#a7c46a,#6f9a3e)"></div>
    <h3>Outdoor Bootcamp</h3>
    <p>Magna aliquam erat volutpat. Ut niml ad minim veniam, quis naullamcorper suscipit commodo consequat.</p>
    <span class="arrow-box"><svg width="10" height="14" viewBox="0 0 10 14"><path d="M2 1l6 6-6 6" fill="none" stroke="#fff" stroke-width="2"/></svg></span>
  </article>

  <article class="abs service-card" style="left:797px">
    <div class="service-img" role="img" aria-label="Small group training session outdoors on grass" style="background:linear-gradient(180deg,#9bb07a,#7a6a55)"></div>
    <h3>Small Group</h3>
    <p>Magna aliquam erat volutpat. Ut niml ad minim veniam, quis naullamcorper suscipit commodo consequat.</p>
    <span class="arrow-box"><svg width="10" height="14" viewBox="0 0 10 14"><path d="M2 1l6 6-6 6" fill="none" stroke="#fff" stroke-width="2"/></svg></span>
  </article>

  <a class="abs btn btn-dark services-btn">View All Services <span class="arrow-dot"><svg width="12" height="12" viewBox="0 0 12 12"><path d="M2 6h8M7 3l3 3-3 3" fill="none" stroke-width="1.8"/></svg></span></a>
</section>

<section>
  <div class="abs videos" role="img" aria-label="Bright gym interior with large windows, softly faded"></div>
  <h2 class="abs section-title videos-title">Videos And Programs</h2>
  <div class="abs title-rule videos-rule"></div>
  <div class="abs coach-photo" role="img" aria-label="Trainer in a grey vest writing on a clipboard"></div>
  <ul class="abs program-list">
    <li>Lorem ipsum dolor sit amet, consectetur adipiscing elit.</li>
    <li>Cras sagittis neque at nulla congue, a pulvinar turpis .</li>
    <li>Nunc consequat tortor id lorem mattis egestas.</li>
    <li>Suspendisse tristique leo sit amet magna consequat &nbsp;vitae dolor.</li>
    <li>Aliquam placerat dui sit amet nunc vehicula, et nisl sodales.</li>
    <li>Morbi faucibus metus vel erat pharetra accumsan.</li>
    <li>Nullam finibus tellus vitae ipsum tincidunt laoreet.</li>
    <li>Morbi et magna elementum, lobortis risus non, &nbsp;arcu.</li>
  </ul>
  <div class="abs video-frame" role="img" aria-label="Video still of a bootcamp group doing crunches outdoors">
    <span class="play"><svg width="16" height="18" viewBox="0 0 16 18"><path d="M3 2l11 7-11 7z" fill="#111"/></svg></span>
  </div>
  <a class="abs videos-link">View All Videos <span class="arrow-dot"><svg width="12" height="12" viewBox="0 0 12 12"><path d="M2 6h8M7 3l3 3-3 3" fill="none" stroke-width="1.8"/></svg></span></a>
</section>

<section>
  <h2 class="abs section-title blog-title">Latest Blog</h2>
  <div class="abs title-rule blog-rule"></div>

  <article class="abs blog-card" style="left:99px">
    <div class="blog-img" role="img" aria-label="Woman doing push-ups on grass in a park" style="background:linear-gradient(180deg,#9cc06a,#4f7e2e)"></div>
    <div class="blog-body">
      <h3>Magna aliquam erat volutpal Ut niml ad minim</h3>
      <div class="blog-date">Posted May &nbsp;12th, 2016</div>
      <p>Lorem ipsum dolor sit a consectetuer adipiscing elit,sed diam nonumm nibh euismod tincid laoreet d magnaautem praesent luptatum feugait...</p>
    </div>
    <span class="arrow-box"><svg width="10" height="14" viewBox="0 0 10 14"><path d="M2 1l6 6-6 6" fill="none" stroke="#fff" stroke-width="2"/></svg></span>
  </article>

  <article class="abs blog-card" style="left:624px">
    <div class="blog-img" role="img" aria-label="Trainer measuring a client's waist in a studio" style="background:linear-gradient(180deg,#3a3a3a,#b08a78)"></div>
    <div class="blog-body">
      <h3>Magna aliquam erat volutpal Ut niml ad minim</h3>
      <div class="blog-date">Posted May &nbsp;12th, 2016</div>
      <p>Lorem ipsum dolor sit a consectetuer adipiscing elit,sed diam nonumm nibh euismod tincid laoreet d magnaautem praesent luptatum feugait...</p>
    </div>
    <span class="arrow-box"><svg width="10" height="14" viewBox="0 0 10 14"><path d="M2 1l6 6-6 6" fill="none" stroke="#fff" stroke-width="2"/></svg></span>
  </article>
</section>

<footer>
  <div class="abs site-footer"></div>

  <div class="abs footer-col" style="left:103px;top:2305px">
    <h4>Quick Links</h4>
    <ul class="footer-links"><li>Home</li><li>About Us</li><li>Services</li><li>Blog</li><li>Contact</li></ul>
  </div>

  <div class="abs footer-col" style="left:307px;top:2305px">
    <h4>Contact Us</h4>
    <ul class="contact-list">
      <li><svg width="12" height="16" viewBox="0 0 12 16"><path d="M6 0a6 6 0 016 6c0 4-6 10-6 10S0 10 0 6a6 6 0 016-6z" fill="#d6d6d6"/><circle cx="6" cy="6" r="2.2" fill="#2f2f2f"/></svg><span>Lorem ipsum dolor sit a consectetuer,<br>consectetuer, NC1234</span></li>
      <li><svg width="14" height="14" viewBox="0 0 24 24"><path d="M6 2l4 4-2 3c1 3 4 6 7 7l3-2 4 4-3 4C10 21 3 14 2 5z" fill="#d6d6d6"/></svg><span>123. 456. 7890</span></li>
      <li><svg width="14" height="14" viewBox="0 0 14 14"><rect x="3" y="0" width="8" height="4" fill="#d6d6d6"/><rect x="0" y="5" width="14" height="6" fill="#d6d6d6"/><rect x="3" y="9" width="8" height="5" fill="#d6d6d6"/></svg><span>123. 456. 7890</span></li>
      <li><svg width="14" height="12" viewBox="0 0 14 12"><rect width="14" height="12" fill="#d6d6d6"/><path d="M0 0l7 6 7-6" fill="none" stroke="#2f2f2f" stroke-width="1.4"/></svg><span>info@vorelan.com</span></li>
    </ul>
  </div>

  <div class="abs footer-col" style="left:576px;top:2305px">
    <h4 style="width:216px">Quick Contact</h4>
    <div class="field" style="margin-top:12px;height:29px">Name</div>
    <div class="field" style="margin-top:7px;height:46px">Message</div>
    <a class="btn btn-dark submit">SUBMIT <span class="arrow-dot"><svg width="12" height="12" viewBox="0 0 12 12"><path d="M2 6h8M7 3l3 3-3 3" fill="none" stroke-width="1.8"/></svg></span></a>
  </div>

  <div class="abs footer-brand"><span class="brand-mark"></span><span class="brand-name">VORELAN</span></div>

  <div class="abs bottom-bar"></div>
  <p class="abs copyright">© 2016. <b>VORELAN</b>. All Right Reserved</p>
  <div class="abs follow-tab"><span class="label">Follow Us :</span><div class="social"><span></span><span></span><span></span><span></span></div></div>
</footer>

</body>
</html>
```